Veldmark Supplies Business Card

Professional business card that stand out to our potential customers. Front and back with clean modern design

Industry/Entity Type

Oil and gas

Contact Information for Business Card

Name, address, website , office phone and cell number

Requirements
Must have
• Editable files for each employee

```html
<!DOCTYPE html>
<html lang="en">
<head>
<meta charset="utf-8">
<title>Veldmark Supplies Business Card</title>
<link href="https://fonts.googleapis.com/css2?family=Arimo:wght@400;700&display=swap" rel="stylesheet">
<style>
  :root {
    --stage: #3b3b3b;
    --card-dark: #2d2d2d;
    --card-light: #ffffff;
    --brand-red: #f20a0a;
    --brand-blue: #0aa6cf;
    --ink: #3a3a3a;
    --rule: #cfcfcf;
  }
  * { box-sizing: border-box; margin: 0; padding: 0; }
  html, body {
    width: 1200px; height: 689px; overflow: hidden;
    background: var(--stage);
    font-family: "Arimo", Arial, sans-serif;
  }
  .stage { position: relative; width: 1200px; height: 689px; }
  .card {
    position: absolute; top: 190px; width: 520px; height: 300px;
    border-radius: 16px; overflow: hidden;
  }
  .card-back { left: 45px; background: var(--card-dark); }
  .card-front { left: 635px; background: var(--card-light); }

  .brand {
    display: flex; align-items: center; gap: 10px;
    font-weight: 700; color: var(--brand-red); letter-spacing: 0.5px;
    text-transform: uppercase; white-space: nowrap;
  }
  .brand-mark { width: 14px; height: 14px; background: var(--brand-blue); }
  .card-back .brand {
    position: absolute; left: 0; right: 0; top: 134px;
    justify-content: center; font-size: 28px;
  }
  .card-back .brand-mark { width: 22px; height: 22px; }

  .card-front .brand {
    position: absolute; right: 30px; top: 34px; font-size: 18px;
  }
  .top-rule {
    position: absolute; right: 30px; top: 70px; width: 230px;
    border-top: 1px solid var(--rule);
  }
  .address {
    position: absolute; right: 30px; top: 84px; text-align: right;
    font-size: 13px; line-height: 1.45; color: var(--ink);
  }
  .person { position: absolute; left: 30px; top: 138px; }
  .person-name { font-size: 26px; font-weight: 700; color: var(--brand-red); }
  .person-title { font-size: 14px; color: var(--brand-blue); margin-top: 2px; }
  .person-rule { width: 230px; border-top: 1px solid var(--rule); margin: 10px 0 8px; }
  .phones { list-style: none; font-size: 14px; color: var(--ink); }
  .phones li { display: flex; align-items: center; gap: 8px; line-height: 1.6; }
  .phones svg { width: 13px; height: 13px; fill: var(--brand-red); }

  .footer-band {
    position: absolute; left: 0; right: 0; bottom: 0; height: 32px;
  }
  .band-email {
    position: absolute; left: 0; top: 0; bottom: 0; width: 330px;
    background: var(--brand-red);
    clip-path: polygon(0 0, 100% 0, 96% 100%, 0 100%);
    color: #fff; font-size: 13px; display: flex; align-items: center; padding-left: 30px;
  }
  .band-web {
    position: absolute; right: 0; top: 0; bottom: 0; width: 200px;
    background: var(--brand-blue);
    clip-path: polygon(6% 0, 100% 0, 100% 100%, 0 100%);
    color: #fff; font-size: 13px; display: flex; align-items: center;
    justify-content: flex-end; padding-right: 30px;
  }
</style>
</head>
<body>
<main class="stage">
  <section class="card card-back" aria-label="Card back">
    <div class="brand"><span class="brand-mark"></span>Veldmark Supplies</div>
  </section>

  <section class="card card-front" aria-label="Card front">
    <div class="brand"><span class="brand-mark"></span>Veldmark Supplies</div>
    <div class="top-rule"></div>
    <p class="address">412 Cedar Ridge Road<br>Calgary, Canada 34120</p>

    <div class="person">
      <h1 class="person-name">Daniel Hartley</h1>
      <p class="person-title">President</p>
      <div class="person-rule"></div>
      <ul class="phones">
        <li>
          <svg viewBox="0 0 24 24" aria-label="Office phone"><path d="M6.6 10.8a15.1 15.1 0 0 0 6.6 6.6l2.2-2.2a1 1 0 0 1 1-.25 11.4 11.4 0 0 0 3.6.57 1 1 0 0 1 1 1V20a1 1 0 0 1-1 1A17 17 0 0 1 3 4a1 1 0 0 1 1-1h3.5a1 1 0 0 1 1 1c0 1.25.2 2.45.57 3.6a1 1 0 0 1-.25 1z"/></svg>
          555-214-7390
        </li>
        <li>
          <svg viewBox="0 0 24 24" aria-label="Mobile phone"><path d="M7 1h10a2 2 0 0 1 2 2v18a2 2 0 0 1-2 2H7a2 2 0 0 1-2-2V3a2 2 0 0 1 2-2zm0 3v15h10V4z"/></svg>
          555-862-1047
        </li>
      </ul>
    </div>

    <div class="footer-band">
      <div class="band-email">info@veldmarksupplies.com</div>
      <div class="band-web">www.veldmarksupplies.com</div>
    </div>
  </section>
</main>
</body>
</html>
```